Ridgeline Journeys business card

please see website
www.ridgelinejourneys.comau

info needed on card
Curtis Halvey
Ph
email
Adventure Riding GPS trails

please use my logo and colours off my site

Curtis Halvey
curtis@ridgelinejourneys.com

```html
<!DOCTYPE html>
<html lang="en">
<head>
<meta charset="utf-8">
<title>Ridgeline Journeys – Business Card</title>
<link rel="stylesheet" href="https://fonts.googleapis.com/css2?family=Open+Sans:ital,wght@0,400;0,600;0,800;1,400&display=swap">
<style>
  :root {
    --page: #e4e0db;
    --frost-light: #f4f5f6;
    --frost-dark: #d6d9dc;
    --ink: #111111;
    --night: #0d0d0d;
    --gold: #e9b21c;
    --gold-deep: #c88a0c;
    --name: #c9bc2b;
    --contact: #bdb8ae;
    --tagline: #a69f8a;
  }
  * { margin: 0; padding: 0; box-sizing: border-box; }
  html, body {
    width: 1200px; height: 969px; overflow: hidden;
    background: var(--page);
    font-family: "Open Sans", Arial, sans-serif;
  }
  .card {
    position: absolute; left: 100px; top: 200px;
    width: 1000px; height: 568px;
    background: linear-gradient(160deg, var(--frost-light), var(--frost-dark));
    box-shadow: 0 18px 40px rgba(0,0,0,.18);
    overflow: hidden;
  }
  .card-wave { position: absolute; inset: 0; width: 1000px; height: 568px; }
  .brand {
    position: absolute; left: 64px; top: 70px;
    display: flex; align-items: center; gap: 22px;
  }
  .brand-dot { width: 92px; height: 92px; border-radius: 50%; background: var(--gold); }
  .brand-name {
    font-weight: 800; font-size: 42px; line-height: 44px;
    color: var(--ink); text-transform: uppercase; letter-spacing: .5px;
  }
  .contact {
    position: absolute; right: 58px; top: 282px;
    text-align: right;
  }
  .contact-name {
    font-size: 33px; font-weight: 400; color: var(--name);
    margin-bottom: 14px;
  }
  .contact-line {
    display: flex; justify-content: flex-end; align-items: center; gap: 18px;
    font-size: 22px; color: var(--contact); height: 38px;
  }
  .contact-icon { width: 24px; height: 24px; fill: var(--gold); }
  .tagline {
    margin-top: 12px; margin-right: 0;
    font-size: 25px; font-style: italic; color: var(--tagline);
  }
</style>
</head>
<body>
  <div class="card">
    <svg class="card-wave" viewBox="0 0 1000 568" aria-hidden="true">
      <defs>
        <linearGradient id="goldBand" x1="0" y1="0" x2="1" y2="0">
          <stop offset="0" stop-color="var(--gold-deep)"/>
          <stop offset=".5" stop-color="var(--gold)"/>
          <stop offset="1" stop-color="var(--gold)"/>
        </linearGradient>
      </defs>
      <path d="M0,396 C150,440 230,512 330,504 C520,490 620,180 1000,124 L1000,568 L0,568 Z" fill="#f7f7f7"/>
      <path d="M0,412 C150,456 230,528 330,520 C520,506 620,196 1000,138 L1000,568 L0,568 Z" fill="url(#goldBand)"/>
      <path d="M0,440 C150,480 230,548 330,540 C520,526 620,216 1000,158 L1000,568 L0,568 Z" fill="var(--night)"/>
    </svg>

    <div class="brand">
      <div class="brand-dot"></div>
      <div class="brand-name">Ridgeline<br>Journeys</div>
    </div>

    <div class="contact">
      <div class="contact-name">Curtis Halvey</div>
      <div class="contact-line">689 512 0746
        <svg class="contact-icon" viewBox="0 0 24 24"><path d="M6.6 10.8a15 15 0 0 0 6.6 6.6l2.2-2.2c.3-.3.7-.4 1-.2 1.1.4 2.3.6 3.6.6.6 0 1 .4 1 1V20c0 .6-.4 1-1 1A17 17 0 0 1 3 4c0-.6.4-1 1-1h3.5c.6 0 1 .4 1 1 0 1.3.2 2.5.6 3.6.1.3 0 .7-.2 1z"/></svg>
      </div>
      <div class="contact-line">curtis@ridgelinejourneys.com
        <svg class="contact-icon" viewBox="0 0 24 24"><path d="M2 5h20v14H2z M2 5l10 8 10-8" fill="var(--gold)" stroke="var(--night)" stroke-width="1.5"/></svg>
      </div>
      <div class="contact-line">www.ridgelinejourneys.comau
        <svg class="contact-icon" viewBox="0 0 24 24"><circle cx="12" cy="12" r="10"/><path d="M7 7c2 1 3 0 4 2s-1 3 0 5 3 1 3 4M15 4c0 2 2 3 4 3" fill="none" stroke="var(--night)" stroke-width="1.6"/></svg>
      </div>
      <div class="tagline">Adventure Riding GPS trails</div>
    </div>
  </div>
</body>
</html>
```